Flyer design for retail store owners

i would need to have a flyer design for my retail shop customers to show that I am a mailbox store that has all major shipping vendors to for their shipping needs. Ensuring that they can take advantage of opening a house account at the store and billed monthly, word document has all the details. Please use stock images for the notary public, passport photos, mailbox brass pictures of my actual mailboxes are listed in the pictures. I need to make it POP and WOW these retail store owners as I am using it to advertise the business

```html
<!DOCTYPE html>
<html lang="en">
<head>
<meta charset="utf-8">
<title>Mailbox Rental &amp; Pack and Ship Flyers</title>
<link rel="stylesheet" href="https://fonts.googleapis.com/css2?family=Anton&family=Arimo:wght@400;700&display=swap">
<style>
  :root {
    --bg: #ece8f1;
    --paper: #ffffff;
    --gold: #c8955a;
    --gold-tab: #d3a167;
    --peach: #fcc98b;
    --peach-light: #fde3bf;
    --grey-box: #ebebeb;
    --ink: #111111;
    --text: #222222;
  }
  * { box-sizing: border-box; margin: 0; padding: 0; }
  html, body { width: 1200px; height: 1200px; overflow: hidden; }
  body { background: var(--bg); font-family: "Arimo", Arial, sans-serif; color: var(--text); position: relative; }

  .flyer { position: absolute; top: 237px; width: 560px; height: 725px; background: var(--paper); overflow: hidden; box-shadow: 0 6px 24px rgba(0,0,0,.12); }
  .flyer--mailbox { left: 30px; }
  .flyer--ship { left: 610px; }
  .abs { position: absolute; }
  .photo { position: absolute; }

  /* Mailbox flyer */
  .corner-accent { position: absolute; top: 0; right: 0; }
  .title-bar { left: 14px; top: 62px; width: 20px; height: 125px; background: var(--gold); }
  .headline { font-family: "Anton", Impact, sans-serif; line-height: 1; letter-spacing: -1px; white-space: nowrap; }
  .headline--black { left: 46px; top: 50px; font-size: 64px; color: var(--ink); }
  .headline--gold { left: 60px; top: 128px; font-size: 50px; color: var(--gold); }
  .intro { left: 46px; top: 196px; width: 240px; font-size: 10.5px; line-height: 14px; text-align: justify; }
  .mailbox-photo { left: 302px; top: 36px; width: 228px; height: 200px; background: linear-gradient(135deg, #d9ad72, #b98a4f); }
  .promo-band { left: 0; top: 358px; width: 560px; height: 190px; background: var(--peach); }
  .notary-frame { left: 330px; top: 250px; width: 230px; height: 200px; background: var(--peach); }
  .notary-photo { left: 318px; top: 262px; width: 222px; height: 170px; background: linear-gradient(135deg, #6d6d6d, #1d1d1d); border: 6px solid var(--paper); }
  .tab { background: var(--gold-tab); color: #fff; font-weight: 700; font-size: 12px; padding: 6px 10px; letter-spacing: .2px; white-space: nowrap; }
  .tab--promo { left: 50px; top: 352px; }
  .promo-text { left: 50px; top: 386px; width: 260px; font-size: 10.5px; line-height: 14px; text-align: justify; }
  .deals-box { left: 300px; top: 548px; width: 260px; height: 127px; background: var(--grey-box); }
  .tab--deals { left: 50px; top: 540px; }
  .deal-list { list-style: none; font-size: 10.5px; line-height: 13px; }
  .deal-list li { position: relative; padding-left: 16px; margin-bottom: 6px; }
  .deal-list li::before { content: ""; position: absolute; left: 0; top: 3px; width: 7px; height: 7px; border-radius: 50%; background: var(--gold); }
  .deal-list--left { left: 50px; top: 577px; width: 238px; }
  .deal-list--right { left: 312px; top: 560px; width: 238px; }
  .footer-band { left: 0; bottom: 0; width: 560px; height: 50px; background: var(--gold); color: #fff; font-weight: 700; font-size: 16px; display: flex; align-items: center; justify-content: center; }

  /* Pack & ship flyer */
  .kicker { left: 40px; top: 48px; font-family: "Anton", Impact, sans-serif; font-size: 34px; color: var(--gold); line-height: 1; }
  .ship-title { left: 38px; top: 84px; font-size: 72px; color: var(--ink); }
  .ship-sub { left: 40px; top: 168px; width: 290px; font-size: 16px; line-height: 20px; color: var(--ink); }
  .ship-band { left: 0; top: 225px; width: 560px; height: 130px; background: var(--peach); }
  .ship-text { left: 30px; top: 245px; width: 300px; font-size: 11.5px; line-height: 15px; }
  .door-photo { left: 345px; top: 140px; width: 200px; height: 205px; background: linear-gradient(135deg, #d7ab62, #a87b3c); border: 6px solid var(--paper); }
  .slot-photo { left: 20px; top: 372px; width: 205px; height: 130px; background: linear-gradient(135deg, #8c9197, #5b6066); }
  .passport-photo-a { left: 240px; top: 372px; width: 300px; height: 130px; background: linear-gradient(135deg, #e2e2e2, #b9b9b9); }
  .passport-photo-b { left: 20px; top: 512px; width: 205px; height: 105px; background: linear-gradient(135deg, #dcdcdc, #aeb4b8); }
  .rural-photo { left: 240px; top: 512px; width: 300px; height: 105px; background: linear-gradient(135deg, #9ec7e6, #e07a5f 55%, #7da45a); }
  .partners-line { left: 20px; top: 630px; width: 530px; font-size: 11.5px; font-weight: 700; color: var(--gold); white-space: nowrap; }
  .partner-row { left: 20px; top: 662px; width: 520px; display: flex; justify-content: space-between; }
  .partner-name { display: flex; align-items: center; gap: 6px; font-size: 14px; font-weight: 700; color: #444; }
  .partner-name::before { content: ""; width: 10px; height: 10px; background: var(--gold); }
  .ship-foot { left: 0; bottom: 0; width: 560px; height: 18px; background: var(--gold); }
</style>
</head>
<body>

<section class="flyer flyer--mailbox">
  <svg class="corner-accent" width="260" height="200" viewBox="0 0 260 200"><polygon points="0,0 260,0 260,195" fill="var(--peach-light)"/></svg>
  <div class="abs title-bar"></div>
  <h1 class="abs headline headline--black">RENTING</h1>
  <h2 class="abs headline headline--gold">A MAIL BOX</h2>
  <div class="photo mailbox-photo" role="img" aria-label="Brass wall-mounted bank of rental mailboxes"></div>
  <p class="abs intro">is one of the most efficient and cost saving methods for receiving your mail and packages. Instead of having to worry about private security, weather conditions, sorting, and deliveries; all you have to do is pick-up your mail from our secured facility each day except Sundays. You will get a notification when mail arrives whether envelope or package, it will be scanned in daily which other mailbox stores do not offer! We offer onsite Notary Public with no appointments and onsite Passport Photos and can ship out same day.</p>

  <div class="abs promo-band"></div>
  <div class="abs notary-frame"></div>
  <div class="photo notary-photo" role="img" aria-label="Notary public signing and stamping documents at a desk"></div>
  <div class="abs tab tab--promo">MAIN PROMOTION:</div>
  <p class="abs promo-text">Now renting mailboxes on Maplewood Commons Shopping Center. We are offering all Maplewood Commons shopping center owners/employees an exclusive promo deal! $12 a month for 6-12 months leases! You get a mailbox in the shop, a book of stamps(20 count), 3 notarizations by appointment, 100 copies of black and white, and 100 copies of color. Please see associate for sign up!</p>

  <div class="abs deals-box"></div>
  <div class="abs tab tab--deals">CHECK OUT THESE OTHER DEALS!</div>
  <ul class="abs deal-list deal-list--left">
    <li>As a retail owner, you know how important it is to keep your customers coming back - you will get 20% discount for printing services.</li>
    <li>We duplicate keys for $2/each, our regular price charge is $4/each. Save up to 50%!</li>
    <li>Lamination is also discounted at 10% off.</li>
  </ul>
  <ul class="abs deal-list deal-list--right">
    <li>10% off retail supplies ... must be minimum of 10$</li>
    <li>For house accounts -a 5% discount will be deducted monthly of billing change to invoicing PLUS we're giving another 5% of the discount if you upgrade and sign up for mailbox. Great right?</li>
  </ul>
  <div class="abs footer-band">Take advantage of this limited time offer now!</div>
</section>

<section class="flyer flyer--ship">
  <div class="abs kicker">AT SWIFT PARCEL</div>
  <h1 class="abs headline ship-title">PACK &amp; SHIP</h1>
  <p class="abs ship-sub">our goal is to make your shipping experience as convenient as possible.</p>
  <div class="abs ship-band"></div>
  <p class="abs ship-text">Whether you are shipping packages, documents, or packages, we are here to help. Whether you want to track your package or estimate the price of your package, it is easy for you. We are ready to handle all of your postal services! Get also the services you need; printing, copying, and stop in to purchase postage or shipping materials.</p>
  <div class="photo door-photo" role="img" aria-label="Brass mailbox with the door open"></div>

  <div class="photo slot-photo" role="img" aria-label="Brass letter slot on a grey front door"></div>
  <div class="photo passport-photo-a" role="img" aria-label="Sheet of passport photos"></div>
  <div class="photo passport-photo-b" role="img" aria-label="Second sheet of passport photos"></div>
  <div class="photo rural-photo" role="img" aria-label="Colourfully painted mailbox on a wooden post"></div>

  <p class="abs partners-line">Our service point partners are ParcelJet, BrownLine, National Post, and GlobeDash.</p>
  <div class="abs partner-row">
    <span class="partner-name">ParcelJet</span>
    <span class="partner-name">BrownLine</span>
    <span class="partner-name">National Post</span>
    <span class="partner-name">GlobeDash</span>
  </div>
  <div class="abs ship-foot"></div>
</section>

</body>
</html>
```